Business Card: RW Office Partners - Your organised problem solver

Business Name: RW Office Partners
Website: www.rwofficepartners.com.au
Email: marisol@rwofficepartners.com.au
Mobile: 61 482 907 236
Facebook: @rwofficepartners
Instrgram: @rwofficepartners

Brading Colours:
HEX
#986474
#ddccd3
#7a8498
#c9d8e4
#000000
#ffffff

Tag Line: Your dependable admin partner

Link to DRAFT website:
https://deskhelpcollective.wixsite.com/rw-office-partners

About Page from the website:
My name is Marisol Wrenfield, and I would love to assist you to become more productive in your day to day and achieve your business and personal goals.
My mission is to give you time, time to work on the important tasks of your business or to be able to spend more time with your family. I will take on the tasks you don’t have time for, don’t know well or simply don’t like to do.
I have an extensive background in Administration, Tender Coordination, Document Control, WHS and Quality Management working primarily in the Construction, Mining and Corporate World.
I am passionate about being organised, having order and making things in your life (and mine) easier! I love to watch something unfold and grow into something amazing! I am known for being the go-to problem solver, the organiser of all things, producing high standards of work even under pressure. I’m also a confident communicator, and I understand that you’re busy running your business.

Target Market(s)

Small to Medium Business who require assistance in their business by a virtual assistant.

Industry/Entity Type

Virtual Assistant

Contact Information for Business Card

Mobile: 61 482 907 236

Font styles to use
Sans Serif

Colors
ffffff

Requirements
Must have
• Branding Colours as outlined.
Contact Details as outlined.
Logo as provided.
Proper contact details - mobile, facebook, instragm, website.
Simple, Elegant, very clean looking.
Should not have
• Note cute with pictures.
Not too girly as still want to market to construction companies.

```html
<!DOCTYPE html>
<html lang="en">
<head>
<meta charset="utf-8">
<title>RW Office Partners – Business Card</title>
<link rel="stylesheet" href="https://fonts.googleapis.com/css2?family=Roboto:wght@400;500;700&display=swap">
<style>
  :root {
    --mauve: #8b5d6f;
    --mauve-brand: #986474;
    --slate: #7a8498;
    --ink: #3d3d3d;
    --paper: #fbfbfb;
    --backdrop: #686565;
    --white: #ffffff;
  }
  * { margin: 0; padding: 0; box-sizing: border-box; }
  html, body { width: 1200px; height: 1200px; overflow: hidden; }
  body {
    background: var(--backdrop);
    font-family: "Roboto", Arial, sans-serif;
    position: relative;
  }
  .card {
    position: absolute;
    width: 712px;
    height: 418px;
    border-radius: 24px;
    overflow: hidden;
  }
  .card--front { left: 238px; top: 119px; background: var(--mauve); }
  .card--back { left: 232px; top: 645px; background: var(--paper); }

  .brand-name {
    font-family: "Roboto", Arial, sans-serif;
    font-weight: 500;
    text-transform: uppercase;
    letter-spacing: 1px;
    line-height: 1.0;
  }
  .card--front .brand-name {
    position: absolute;
    left: 0; right: 0; top: 170px;
    text-align: center;
    color: var(--white);
    font-size: 48px;
  }
  .card--back .brand-name {
    position: absolute;
    left: 38px; top: 54px;
    color: var(--mauve);
    font-size: 44px;
  }

  .holder { position: absolute; left: 38px; top: 236px; }
  .holder__name { color: var(--mauve); font-weight: 700; font-size: 27px; }
  .holder__role { color: var(--ink); font-size: 18px; margin-top: 6px; }

  .contacts { position: absolute; left: 336px; top: 235px; list-style: none; }
  .contacts li {
    display: flex; align-items: center; gap: 12px;
    height: 26px; font-size: 18px; color: var(--ink);
  }
  .contacts svg { width: 18px; height: 18px; flex: none; }

  .socials { position: absolute; left: 39px; top: 339px; list-style: none; }
  .socials li {
    display: flex; align-items: center; gap: 13px;
    height: 24px; font-size: 17px; color: var(--ink);
  }
  .socials .mark {
    width: 14px; height: 14px; border-radius: 3px; background: var(--mauve); flex: none;
  }

  .footer-band { position: absolute; left: 0; bottom: 0; width: 712px; height: 52px; }
  .tagline {
    position: absolute; left: 336px; bottom: 17px;
    color: var(--white); font-size: 18px;
  }
</style>
</head>
<body>
  <section class="card card--front" aria-label="Card front">
    <div class="brand-name">RW Office<br>Partners</div>
  </section>

  <section class="card card--back" aria-label="Card back">
    <div class="brand-name">RW Office<br>Partners</div>

    <div class="holder">
      <div class="holder__name">Marisol Wrenfield</div>
      <div class="holder__role">Virtual Assistant</div>
    </div>

    <ul class="contacts">
      <li>
        <svg viewBox="0 0 18 18" aria-hidden="true"><path fill="#8b5d6f" d="M2 6c0-2 3-3 7-3s7 1 7 3v1h-4V6H6v1H2zM4 9l2-2h6l2 2v6H4z"/><circle cx="9" cy="11.5" r="1.8" fill="#fbfbfb"/></svg>
        61 482 907 236
      </li>
      <li>
        <svg viewBox="0 0 18 18" aria-hidden="true"><rect x="1" y="4" width="16" height="11" fill="#8b5d6f"/><path d="M1 4l8 6 8-6" fill="none" stroke="#fbfbfb" stroke-width="1.4"/></svg>
        marisol@rwofficepartners.com.au
      </li>
      <li>
        <svg viewBox="0 0 18 18" aria-hidden="true"><circle cx="9" cy="9" r="7.5" fill="#8b5d6f"/><g fill="none" stroke="#fbfbfb" stroke-width="1"><ellipse cx="9" cy="9" rx="3" ry="7.5"/><path d="M1.5 9h15M3 5h12M3 13h12"/></g></svg>
        www.rwofficepartners.com.au
      </li>
    </ul>

    <ul class="socials">
      <li><span class="mark" aria-hidden="true"></span>@rwofficepartners</li>
      <li><span class="mark" aria-hidden="true"></span>@rwofficepartners</li>
    </ul>

    <svg class="footer-band" viewBox="0 0 712 52" aria-hidden="true">
      <rect x="0" y="33" width="310" height="19" fill="#7a8498"/>
      <path d="M292 0H712V52H272L284 6Q286 0 292 0Z" fill="#8b5d6f"/>
    </svg>
    <div class="tagline">Your dependable admin partner</div>
  </section>
</body>
</html>
```